QHX Compliant Dietary Supplement Label for Nutritional Company

We are in need of a label for our line of 20+ dietary supplements that are specifically formulated to balance body chemistry and match the biochemical individuality of our users based on hair tissue mineral analysis.

We have a line of approximately 20 different dietary supplements that will require use of new label in both a small (90 capsule) and large (180 capsule) size. We will start with the initial label in which Product name, Supplement Facts, and Ingredient list will need to be modified for each particular product thereafter.

The label will be placed on a transparent blue bottle with the color of lid being decided after label design. We are open to a transparent light amber bottle with black lid but blue is our preference.

We would like the majority of the label to be blue. Solid blue, fading of blue to darker blue/black, or subtle background designs are welcome with involvement of white and hints of orange. We do not want pictorial images on the label.

Label size:
Small bottle (120cc): Label size ~ 2.25” x 5.875”
Large bottle (200cc): Label size ~ 2.75” x 7.625”

Front:
-Logo near top of label with product name and description in middle and capsule count near the bottom

Right Side:
-Supplement Facts: See current product image below in brief
-Ingredient list: See current product image below in brief
-Manufactured for: See image below (This is on the left side of our current bottle and would like it moved to the bottom of the right side)

Left side:
-Suggested use: See current product image below in brief
-Leave room for possible warning statement
-Leave room for possible lot number printing
-Keep out of the reach of children.

The first files below are our current supplement label with product information. This information is what is needed on the label and will likely need some adjustments as we are updating our line of supplements and changes in QHX requirements.

The following files are the logo files and color palette.

The remaining files are some designs we came across for inspiration.

Thank you.

Target Market(s)

Health Care Profressionals

Industry/Entity Type

Health Care and Nutrition

Requirements
Nice to have
• Product name needs to be on same line in all one color
Should not have
• Pictorial Images

```html
<!DOCTYPE html>
<html lang="en">
<head>
<meta charset="utf-8">
<title>CORTA-VEL Adrenal Supplement Label</title>
<link rel="stylesheet" href="https://fonts.googleapis.com/css2?family=Montserrat:wght@300;400;500;600;700;800&family=Lato:wght@400;700;900&display=swap">
<style>
  :root {
    --navy-deep: #0d1636;
    --navy: #16245a;
    --royal: #2c44a0;
    --brand-blue: #4d72d6;
    --orange: #f47b20;
    --white: #ffffff;
    --facts-ink: #1d2a6b;
  }
  * { box-sizing: border-box; margin: 0; padding: 0; }
  html, body { width: 1200px; height: 906px; overflow: hidden; background: var(--white); }
  body { position: relative; font-family: "Montserrat", Arial, sans-serif; }

  .label {
    position: absolute; left: 30px; top: 235px; width: 1140px; height: 436px;
    background: linear-gradient(170deg, var(--navy-deep) 0%, var(--navy) 45%, var(--royal) 100%);
    border-top: 3px solid var(--orange);
    border-bottom: 10px solid var(--orange);
    box-shadow: 0 4px 8px rgba(0,0,0,.25);
    color: var(--white);
  }

  /* left panel */
  .usage { position: absolute; left: 32px; top: 26px; width: 280px; font-size: 15.5px; line-height: 1.25; padding-bottom: 14px; border-bottom: 2px solid var(--white); }
  .notice { position: absolute; left: 32px; top: 262px; width: 280px; background: var(--white); border: 3px solid var(--orange); border-radius: 6px; color: var(--navy); font-size: 15px; line-height: 1.3; padding: 6px 12px; }
  .notice strong { font-weight: 700; }
  .print-field { position: absolute; left: 32px; width: 280px; font-size: 15px; display: flex; align-items: flex-end; gap: 4px; }
  .print-field span.line { flex: 1; border-bottom: 1px solid var(--white); height: 1px; margin-bottom: 4px; }
  .lot { top: 358px; }
  .exp { top: 386px; }

  /* front panel */
  .brand { position: absolute; left: 420px; width: 300px; top: 72px; text-align: center; }
  .brand-name { display: inline-flex; align-items: center; gap: 8px; font-size: 31px; font-weight: 500; color: var(--brand-blue); letter-spacing: 1px; }
  .brand-dot { width: 14px; height: 14px; border-radius: 50%; background: var(--orange); }
  .brand-sub { font-size: 12px; letter-spacing: 4.5px; margin-top: 2px; }
  .product { position: absolute; left: 360px; width: 420px; top: 170px; text-align: center; }
  .product-name { font-size: 62px; font-weight: 800; letter-spacing: -1px; line-height: 1; }
  .product-desc { font-size: 29px; font-weight: 500; color: var(--orange); margin-top: 10px; letter-spacing: .5px; }
  .count { position: absolute; left: 380px; top: 346px; line-height: 1; }
  .count-num { font-size: 54px; font-weight: 300; }
  .count-unit { font-size: 12px; margin-top: 2px; }
  .category { position: absolute; right: 380px; top: 382px; text-align: right; font-size: 16px; font-weight: 500; line-height: 1.15; }

  /* right panel */
  .facts { position: absolute; left: 832px; top: 34px; width: 276px; background: var(--white); border: 2px solid var(--navy); color: var(--facts-ink); font-family: "Lato", Arial, sans-serif; padding: 4px 6px 5px; font-size: 10.5px; line-height: 1.12; }
  .facts-title { font-size: 25px; font-weight: 900; line-height: 1; }
  .facts-serving { font-size: 11px; font-weight: 700; margin-top: 3px; }
  .bar-thick { height: 6px; background: var(--facts-ink); margin: 4px 0 3px; }
  .bar-mid { height: 4px; background: var(--facts-ink); margin: 2px 0; }
  .facts-row { display: grid; grid-template-columns: 1fr 50px 40px; border-bottom: 1px solid var(--facts-ink); padding: 1px 0; align-items: end; }
  .facts-row .amt, .facts-row .dv { text-align: right; }
  .facts-row .indent { padding-left: 10px; display: block; }
  .facts-head { font-size: 8px; font-weight: 700; border-bottom: 1px solid var(--facts-ink); }
  .facts-foot { font-size: 10.5px; margin-top: 3px; }
  .ingredients { position: absolute; left: 832px; top: 350px; width: 290px; font-size: 10.5px; line-height: 1.15; }
  .ingredients strong, .distributor strong { font-weight: 700; }
  .distributor { position: absolute; left: 832px; top: 384px; width: 290px; font-size: 10.5px; line-height: 1.3; }
</style>
</head>
<body>
  <section class="label" aria-label="CORTA-VEL supplement label">
    <div class="usage">SUGGESTED USE: One capsule daily or as directed by a physician.</div>
    <div class="notice"><strong>NOTICE:</strong> It is advisable to keep this and all supplements out of the reach of children.</div>
    <div class="print-field lot">LOT #: <span class="line"></span></div>
    <div class="print-field exp">EXP: <span class="line"></span></div>

    <div class="brand">
      <div class="brand-name"><span class="brand-dot"></span>NOVA-LYTE</div>
      <div class="brand-sub">LABORATORIES</div>
    </div>
    <div class="product">
      <h1 class="product-name">CORTA-VEL</h1>
      <div class="product-desc">ADRENAL SUPPLEMENT</div>
    </div>
    <div class="count"><div class="count-num">90</div><div class="count-unit">CAPSULES</div></div>
    <div class="category">DIETARY<br>SUPPLEMENT</div>

    <div class="facts">
      <div class="facts-title">Supplement Facts</div>
      <div class="facts-serving">Serving Size: 1 Capsule<br>Servings Per Container 90</div>
      <div class="bar-thick"></div>
      <div class="facts-row facts-head"><span></span><span class="amt">Amount Per Serving</span><span class="dv">% Daily Value</span></div>
      <div class="facts-row"><span>Vitamin C (as ascorbic acid)</span><span class="amt">100 mg</span><span class="dv">111%</span></div>
      <div class="facts-row"><span>Vitamin B5<span class="indent">(as D-calcium pantothenate)</span></span><span class="amt">100 mg</span><span class="dv">2000%</span></div>
      <div class="facts-row"><span>Magnesium (as magnesium amino<span class="indent">acid chelate)</span></span><span class="amt">5 mg</span><span class="dv">1%</span></div>
      <div class="facts-row"><span>Zinc (as zinc amino acid chelate)</span><span class="amt">1 mg</span><span class="dv">9%</span></div>
      <div class="facts-row"><span>Manganese (as manganese<span class="indent">amino acid chelate)</span></span><span class="amt">1 mg</span><span class="dv">43%</span></div>
      <div class="facts-row"><span>Potassium (as potassium<span class="indent">amino acid chelate)</span></span><span class="amt">25 mg</span><span class="dv">1%</span></div>
      <div class="bar-mid"></div>
      <div class="facts-row"><span>Suprarenal (adrenal) powder (bovine)</span><span class="amt">100 mg</span><span class="dv">†</span></div>
      <div class="facts-row"><span>Liver Powder, defatted (bovine)</span><span class="amt">45 mg</span><span class="dv">†</span></div>
      <div class="facts-row"><span>Betain Hydrochloride</span><span class="amt">25 mg</span><span class="dv">†</span></div>
      <div class="bar-mid"></div>
      <div class="facts-foot">† Daily Value not established</div>
    </div>
    <p class="ingredients"><strong>Other Ingredients:</strong> Hypromellose (Vegetable Capsule), Flo-Blend (R) (Organic Rice Fiber)</p>
    <p class="distributor">Distributed by: NOVA-LYTE LABORATORIES, INC.<br>Riverton, AZ 85999 USA</p>
  </section>
</body>
</html>
```